Indy Film Production Company/Studio

We need a business card designed from an existing logo. We are a digital studio/production company that caters to creating genre entertainment, like Action, Horror, and martial arts. The card along with the logo will be used to Brand the company from letter heads to banners. The design will also be used for postcards and Brochures. It should be professional and masculine.
Updates

Thank you to all the designers who have participated. I'm narrowing down who it will be. Thank you again.

Target Market(s)

Investors, Networks, Producers, and actors

Industry/Entity Type

Film Production

Contact Information for Business Card

Teodoro Valbuena
Producer/Writer/Director
www.kestrelpicturehouse.example

Requirements
Must have
• Website address, plain circle with @kestrelpicturehouse icon and plain circle with @kestrelpicturehouse icon possibly in the back of the card.
Nice to have
• Logline of Company: Follow The Action.

```html
<!DOCTYPE html>
<html lang="en">
<head>
<meta charset="utf-8">
<title>Kestrel Picture House — Business Card</title>
<link href="https://fonts.googleapis.com/css2?family=Montserrat:wght@400;500;800&display=swap" rel="stylesheet">
<style>
  :root {
    --backdrop: #3a3a3a;
    --card: #050505;
    --red: #e3232c;
    --white: #f2f2f2;
    --rule: #d9d9d9;
  }
  * { margin: 0; padding: 0; box-sizing: border-box; }
  html, body {
    width: 1200px; height: 900px; overflow: hidden;
    background: var(--backdrop);
    font-family: "Montserrat", sans-serif;
  }
  .stage { position: relative; width: 1200px; height: 900px; }
  .card {
    position: absolute;
    width: 520px; height: 300px;
    background: var(--card);
    box-shadow: 0 14px 30px rgba(0,0,0,.45);
    color: var(--white);
  }
  .card--front { left: 60px; top: 170px; }
  .card--back  { left: 620px; top: 430px; }

  .brand-name {
    font-weight: 800;
    color: var(--red);
    text-transform: uppercase;
    line-height: 1;
    letter-spacing: 1px;
  }
  .brand-name span { display: block; }
  .card--front .brand-name {
    position: absolute; left: 0; right: 0; top: 70px;
    text-align: center; font-size: 44px;
  }
  .card--front .brand-name .brand-sub { font-size: 22px; margin-top: 8px; letter-spacing: 3px; }

  .front-web {
    position: absolute; left: 0; right: 0; bottom: 62px;
    text-align: center; font-size: 14px; letter-spacing: .5px;
  }
  .front-web .accent { color: var(--red); }

  .social-row {
    position: absolute; left: 0; right: 0; bottom: 30px;
    display: flex; justify-content: center; align-items: center; gap: 8px;
    list-style: none; font-size: 12px; letter-spacing: .3px;
  }
  .social-dot {
    width: 12px; height: 12px; border-radius: 50%;
    background: var(--red); display: inline-block;
  }
  .social-handle { margin-left: 4px; }

  .card--back .brand-name {
    position: absolute; left: 42px; top: 52px;
    font-size: 40px;
  }
  .card--back .brand-name .brand-sub { font-size: 20px; margin-top: 8px; letter-spacing: 3px; }

  .rule { position: absolute; height: 1.5px; background: var(--rule); }
  .rule--top { right: 0; top: 126px; width: 230px; }
  .rule--bottom { left: 0; top: 208px; width: 290px; }

  .person {
    position: absolute; right: 24px; top: 134px; text-align: right;
  }
  .person-name { color: var(--red); font-weight: 500; font-size: 16px; letter-spacing: 1px; text-transform: uppercase; }
  .person-role { font-size: 10px; letter-spacing: 1px; margin-top: 3px; text-transform: uppercase; }

  .contact-list { position: absolute; left: 24px; top: 218px; list-style: none; }
  .contact-list li {
    display: flex; align-items: center; gap: 10px;
    font-size: 13px; line-height: 20px; letter-spacing: .3px;
  }
  .contact-list svg { width: 11px; height: 11px; fill: none; stroke: var(--red); stroke-width: 1.6; }
  .contact-list svg .solid { fill: var(--red); stroke: none; }
</style>
</head>
<body>
<main class="stage">

  <section class="card card--front" aria-label="Card front">
    <h1 class="brand-name"><span>Kestrel</span><span class="brand-sub">Picture House</span></h1>
    <p class="front-web">www.<span class="accent">kestrelpicturehouse</span>.example</p>
    <ul class="social-row" aria-label="Social profiles">
      <li class="social-dot" aria-hidden="true"></li>
      <li class="social-dot" aria-hidden="true"></li>
      <li class="social-handle">@kestrelpicturehouse</li>
    </ul>
  </section>

  <section class="card card--back" aria-label="Card back">
    <h2 class="brand-name"><span>Kestrel</span><span class="brand-sub">Picture House</span></h2>
    <div class="rule rule--top"></div>
    <div class="person">
      <p class="person-name">Teodoro Valbuena</p>
      <p class="person-role">Producer / Writer / Director</p>
    </div>
    <div class="rule rule--bottom"></div>
    <ul class="contact-list">
      <li>
        <svg viewBox="0 0 12 12" aria-hidden="true"><path class="solid" d="M2 1h2.5l1 2.5-1.3 1a6 6 0 0 0 3.3 3.3l1-1.3 2.5 1V10a1 1 0 0 1-1 1A9 9 0 0 1 1 2a1 1 0 0 1 1-1z"/></svg>
        +330 2460-0000
      </li>
      <li>
        <svg viewBox="0 0 12 12" aria-hidden="true"><rect x="1" y="2.5" width="10" height="7"/><path d="M1 2.5l5 4 5-4"/></svg>
        info@kestrelpicturehouse.example
      </li>
      <li>
        <svg viewBox="0 0 12 12" aria-hidden="true"><circle cx="6" cy="6" r="5"/><path d="M1 6h10M6 1c-2.5 3-2.5 7 0 10M6 1c2.5 3 2.5 7 0 10"/></svg>
        www.kestrelpicturehouse.example
      </li>
    </ul>
  </section>

</main>
</body>
</html>
```